Design website for new email startup

We are starting a company called Pingo.QZ (it will live at http://pingo.qz).

We would like the main landing page for our site designed. We have provided a very simple wireframe to help provide direction for the content it should include, but we do not expect the designers to adhere to it at all - we encourage unique ideas. There is some sample text in the wireframe - this does not have to be used, but may provide ideas.

We provide an easy way for people to manage email for a custom domain name. For example if you own "yourhouseword.example" you can point your DNS records to us and we'll make it easy to have emails addressed to your domain get forwarded to your existing email (gmail, etc). Folks running blogs, and other small sites can quickly setup email addresses for their domains and manage them in one place.

(For technical folks, we have you point your dns mx records to us, hence the name. That way all your email hits us and we can redirect it wherever you want. We make it easy to manage a single domain or a bunch of domains. Many domain registrars offer this service for a fee, and have clumsy management tools. We provide a robust simple toolset for free, as well as premium options).

The goal of the landing page is to get folks into the signup flow. The second priority flow is to have them take a look at the premium plan offerings.

We may offer the winning designer additional work for the remainder of the site design.
Updates

I've changed this project to a committed payment.  It is no longer refundable.  Thank you.

Target Market(s)

Bloggers, podcasters, designers, app developers - people who are a little tech savvy.

Industry/Entity Type

It Company

Font styles to use
Sans Serif

Colors

Designer to choose colors to be used in the design.

Requirements
Must have
• A full fidelity mockup (comp) of the landing page including the source file (psd, ai, etc).

Some sort of logo treatment for the pingo.qz brand

A call to action for signup, such as the suggested 'Get Started Here'
Nice to have
• A hip startup feel

Incorporation of the email theme

Give the impression it is simple, easy and fast

```html
<!DOCTYPE html>
<html lang="en">
<head>
<meta charset="utf-8">
<title>Pingo.QZ — email for your domain</title>
<link rel="stylesheet" href="https://fonts.googleapis.com/css2?family=Arimo:wght@400;700&display=swap">
<style>
  :root {
    --teal: #13978a;
    --teal-band: #36968c;
    --teal-button: #3a9a8f;
    --teal-dark: #0f5c55;
    --ink: #333333;
    --muted: #a6a6a6;
    --line: #dcdcdc;
    --footer: #555555;
    --footer-text: #d8d8d8;
    --white: #ffffff;
  }
  * { box-sizing: border-box; margin: 0; padding: 0; }
  html, body { width: 1200px; height: 948px; overflow: hidden; background: var(--white); }
  body { font-family: "Arimo", Arial, sans-serif; color: var(--ink); position: relative; }

  .site-header { position: absolute; left: 140px; top: 40px; width: 918px; height: 40px; }
  .brand { position: absolute; left: 0; top: 0; font-size: 36px; font-weight: 700; color: var(--teal); letter-spacing: 0.5px; line-height: 40px; }
  .main-nav { position: absolute; right: 0; top: 16px; font-size: 13.5px; color: var(--ink); display: flex; gap: 15px; }

  .hero { position: absolute; left: 140px; top: 98px; width: 918px; height: 336px; background: #000; overflow: hidden; }
  .hero-visual { position: absolute; right: 0; top: 0; width: 380px; height: 100%;
    background: radial-gradient(ellipse at 70% 35%, #7fd8c6 0%, #2f8f80 35%, #0d3a34 65%, transparent 85%),
                linear-gradient(90deg, #000 0%, #072a26 40%, #1d6b60 100%); }
  .hero-points { position: absolute; left: 50px; top: 78px; list-style: none; color: var(--white); font-size: 15.5px; }
  .hero-points li { position: relative; padding-left: 25px; height: 32px; line-height: 20px; }
  .hero-points li::before { content: ""; position: absolute; left: 0; top: 4px; width: 12px; height: 12px; border-radius: 50%; background: var(--white); }
  .btn-start { position: absolute; left: 62px; top: 237px; width: 164px; height: 39px; border-radius: 7px; background: var(--teal-button); color: var(--white); font-weight: 700; font-size: 13.5px; line-height: 39px; text-align: center; }
  .slider-dots { position: absolute; left: 415px; top: 276px; display: flex; gap: 11px; }
  .slider-dots span { width: 17px; height: 17px; border: 2.5px solid var(--white); border-radius: 50%; }

  .plans-band { position: absolute; left: 194px; top: 406px; width: 813px; height: 109px; background: var(--teal-band); }
  .plans-shadow { position: absolute; top: 515px; height: 22px; width: 340px;
    background: radial-gradient(ellipse at 50% 0%, rgba(0,0,0,0.28) 0%, rgba(0,0,0,0) 70%); }
  .plans-text { position: absolute; left: 36px; top: 20px; width: 545px; color: var(--white); font-size: 17.5px; line-height: 33px; }
  .btn-compare { position: absolute; right: 22px; top: 33px; width: 176px; height: 43px; border-radius: 6px; background: var(--teal-dark); color: var(--white); font-weight: 700; font-size: 13.5px; line-height: 43px; text-align: center; }

  .guide-card { position: absolute; top: 607px; width: 446px; height: 174px; border: 1px solid var(--line); }
  .guide-card h2 { position: absolute; left: 23px; top: 13px; width: 400px; font-size: 13.5px; font-weight: 400; line-height: 19px; color: #444; }
  .guide-icon { position: absolute; left: 18px; top: 57px; width: 108px; height: 96px; border: 1px solid #cfcfcf; display: flex; align-items: center; justify-content: center; }
  .guide-icon .fill { width: 72px; height: 66px; background: linear-gradient(#3a3a3a, #222); border-radius: 6px; }
  .guide-card p { position: absolute; left: 146px; top: 64px; width: 285px; font-size: 11.5px; line-height: 27px; color: var(--muted); }

  .site-footer { position: absolute; left: 0; top: 839px; width: 1200px; height: 109px; background: var(--footer); }
  .social { position: absolute; left: 50%; top: 18px; transform: translateX(-50%); display: flex; gap: 9px; }
  .social span { width: 38px; height: 38px; border-radius: 50%; border: 3px solid #3d3d3d; }
  .social .s1 { background: #3bb6dc; } .social .s2 { background: #3b5ca8; }
  .social .s3 { background: #5a5a5a; } .social .s4 { background: #e2588f; }
  .copyright { position: absolute; top: 67px; width: 100%; text-align: center; font-size: 11.5px; color: var(--footer-text); }
</style>
</head>
<body>
  <header class="site-header">
    <div class="brand">Pingo.QZ</div>
    <nav class="main-nav"><span>How it work</span><span>|</span><span>Support</span><span>|</span><span>Login</span></nav>
  </header>

  <section class="hero">
    <div class="hero-visual" role="img" aria-label="Glowing teal fiber optic strands behind a large at sign"></div>
    <ul class="hero-points">
      <li>We make email esay.</li>
      <li>Give us five minutes and well get you email from your domain.</li>
      <li>Easily forward mail from your custom domain in name wherever you want it.</li>
      <li>You take the mail well keep the spam.</li>
    </ul>
    <div class="btn-start">GET STARTED FREE</div>
    <div class="slider-dots"><span></span><span></span><span></span></div>
  </section>

  <div class="plans-shadow" style="left:200px"></div>
  <div class="plans-shadow" style="left:670px"></div>
  <section class="plans-band">
    <p class="plans-text">Somewhere we need a link to plan/pricing options,although the free tier is encouraged for initial signup.</p>
    <div class="btn-compare">COMPARE PLANS</div>
  </section>

  <article class="guide-card" style="left:140px">
    <h2>How to configure your Skyvarrow DNS to use pingo.qz</h2>
    <div class="guide-icon"><div class="fill" role="img" aria-label="Icon of a technician holding a wrench"></div></div>
    <p>We provide an easy way for people to manage email for yourhouseword.example" you can point your DNS emails addressed to your domain.....</p>
  </article>
  <article class="guide-card" style="left:611px">
    <h2>Use pingo.qz with your DomainDuck domain registration for reliable email forwarding</h2>
    <div class="guide-icon"><div class="fill" role="img" aria-label="Icon of a document list with a pen"></div></div>
    <p>We provide an easy way for people to manage email for yourhouseword.example" you can point your DNS emails addressed to your domain......</p>
  </article>

  <footer class="site-footer">
    <div class="social"><span class="s1"></span><span class="s2"></span><span class="s3"></span><span class="s4"></span></div>
    <p class="copyright">Copyright 2014 Pingo.QZ.All Right Reseved.</p>
  </footer>
</body>
</html>
```